Website Design Project for Beauty & Wellness Professionals

As background information, I have a website that is focused on Beauty & Wellness Professionals:
- Job Search (www.lumarinovo.com)
- Business Classifieds (negocios.lumarinovo.com)
- Freelancer Classifieds (freelancer.lumarinovo.com)
- Course Reviews (cursos.lumarinovo.com)

All those websites use standard templates.

I need a DESIGN for the HOME PAGE (no coding) of the Website Platform that consolidates the four platforms under the same design.

Website designs that we like:
- quelvox.com
- brintmoor.com

Target Market(s)

Brazilian Professionals from Beauty & Wellness sector

Industry/Entity Type

Business

Requirements
Must have
• Website designs that we like:
- quelvox.com
- brintmoor.com

```html
<!DOCTYPE html>
<html lang="pt">
<head>
<meta charset="utf-8">
<title>Lumarinovo — Home</title>
<link rel="stylesheet" href="https://fonts.googleapis.com/css2?family=Cabin:wght@400;500;600;700&family=PT+Sans:wght@400;700&display=swap">
<style>
  :root {
    --topbar: #6fbfd6;
    --teal: #2f9cbc;
    --teal-dark: #1d7897;
    --footer-top: #5fb0c9;
    --footer-bot: #2a7e9c;
    --footer-strip: #3e93b1;
    --ink: #1b1b1b;
    --text: #3a3a3a;
    --muted: #8a8a8a;
    --line: #dcdcdc;
    --panel: #efefef;
    --orange: #e86f12;
    --orange-light: #f39a3c;
    --green: #3d9a2a;
    --green-dark: #2a7a1c;
    --search-bg: #3c3c3c;
    --white: #ffffff;
  }
  * { box-sizing: border-box; margin: 0; padding: 0; }
  html, body { width: 686px; height: 1200px; overflow: hidden; background: #fff; }
  body { font-family: "PT Sans", sans-serif; color: var(--text); }
  .page { position: relative; width: 686px; height: 1200px; overflow: hidden; }
  .abs { position: absolute; }

  .topbar { left: 0; top: 0; width: 686px; height: 18px; background: var(--topbar); color: #fff; font-size: 7.5px; }
  .topbar .links { position: absolute; right: 58px; top: 4px; letter-spacing: .1px; }
  .topbar .links span { margin: 0 4px; }

  .header { left: 0; top: 18px; width: 686px; height: 66px; background: linear-gradient(#fff, #f6f6f6); }
  .brand { position: absolute; left: 54px; top: 16px; display: flex; align-items: center; gap: 6px; }
  .brand-mark { width: 30px; height: 30px; border-radius: 50%; background: #e79a7e; }
  .brand-name { font-family: "Cabin", sans-serif; font-size: 19px; color: #3a9db6; }
  .social-top { position: absolute; left: 216px; top: 30px; display: flex; gap: 3px; }
  .social-top i { display: block; width: 16px; height: 16px; background: #5b8fb0; border-radius: 2px; }
  .nav { position: absolute; left: 317px; top: 31px; display: flex; font-size: 11px; color: #333; }
  .nav a { color: inherit; text-decoration: none; padding: 0 7px; border-left: 1px solid #ccc; line-height: 13px; }
  .nav a:first-child { border-left: none; padding-left: 0; }

  .hero { left: 0; top: 84px; width: 686px; height: 257px; background: linear-gradient(90deg, #f4f4f4 0%, #ededed 45%, #d9d6d3 70%, #c9c4bf 100%); }
  .hero-photo { position: absolute; right: 104px; top: 0; width: 160px; height: 257px; background: linear-gradient(180deg, #8a6a5a 0%, #b39a8c 35%, #a8b0b8 70%, #d8d8d8 100%); border-radius: 40px 0 0 0; opacity: .75; }
  .hero-kicker { position: absolute; left: 101px; top: 92px; font-family: "Cabin", sans-serif; font-weight: 600; font-size: 19px; color: var(--ink); }
  .hero-title { position: absolute; left: 101px; top: 115px; font-family: "Cabin", sans-serif; font-weight: 700; font-size: 29px; color: var(--ink); letter-spacing: -.3px; }
  .search { position: absolute; left: 101px; top: 158px; width: 486px; height: 42px; background: var(--search-bg); border-radius: 2px; }
  .search .field { position: absolute; top: 10px; height: 21px; background: #fff; border: 1px solid #ccc; font-size: 9px; color: #aaa; padding: 5px 9px; }
  .search .select { left: 8px; width: 80px; color: #444; background: linear-gradient(#fff, #e4e4e4); }
  .search .select::after { content: ""; position: absolute; right: 7px; top: 8px; border: 4px solid transparent; border-top-color: #555; }
  .search .select::before { content: ""; position: absolute; right: 18px; top: 0; width: 1px; height: 19px; background: #ccc; }
  .search .key { left: 94px; width: 181px; }
  .search .loc { left: 279px; width: 125px; }
  .search .btn { position: absolute; left: 410px; top: 10px; width: 65px; height: 22px; background: linear-gradient(#6ec3de, #3a9fc3); color: #fff; font-size: 10px; text-align: center; line-height: 22px; }

  .tabs { left: 175px; top: 363px; display: flex; gap: 5px; }
  .tab { height: 26px; padding: 0 9px; border: 1px solid #ccc; border-bottom: none; background: #ececec; font-size: 9.5px; line-height: 25px; color: #333; }
  .tab.active { background: #fff; height: 27px; }
  .tabs-rule { left: 157px; top: 389px; width: 371px; height: 1px; background: var(--line); }

  .job { left: 155px; width: 343px; }
  .job-logo { position: absolute; left: 0; top: 0; width: 47px; height: 46px; border: 1px solid #e2e2e2; box-shadow: 0 1px 2px rgba(0,0,0,.1); background: #fff; display: flex; align-items: center; justify-content: center; }
  .job-logo i { display: block; width: 33px; height: 33px; }
  .job-title { position: absolute; left: 59px; top: 0; width: 160px; font-size: 9.5px; line-height: 12.5px; color: var(--teal); }
  .job-meta { position: absolute; left: 59px; width: 160px; font-size: 7px; line-height: 10px; color: var(--muted); }
  .job-city { position: absolute; left: 233px; top: 0; font-size: 9.5px; color: #333; }
  .job-region { position: absolute; left: 233px; top: 14px; width: 60px; font-size: 7px; line-height: 10px; color: var(--muted); }
  .job-date { position: absolute; left: 313px; top: 0; font-size: 9.5px; color: #333; }
  .job-year { position: absolute; left: 313px; top: 14px; font-size: 7px; color: var(--muted); }
  .rule { height: 1px; background: #e6e6e6; }

  .pager { left: 219px; top: 611px; width: 256px; height: 26px; background: #eaeaea; display: flex; align-items: center; justify-content: center; gap: 4px; }
  .pager span { height: 15px; min-width: 15px; padding: 0 4px; background: #fff; border: 1px solid #d6d6d6; font-size: 7.5px; line-height: 13px; text-align: center; color: #333; }
  .pager .wide { min-width: 34px; }

  .section-title { font-family: "Cabin", sans-serif; font-weight: 400; font-size: 12px; color: #222; }
  .course { width: 131px; }
  .course-img { width: 131px; height: 88px; }
  .course p { margin-top: 8px; font-size: 7.5px; line-height: 12.5px; color: var(--muted); }
  .btn-orange { display: block; margin-top: 9px; width: 66px; height: 19px; background: linear-gradient(var(--orange-light), var(--orange)); color: #fff; font-size: 7px; text-align: center; line-height: 19px; border-radius: 2px; }
  .divider { left: 75px; top: 852px; width: 520px; height: 1px; background: #e2e2e2; }

  .box { top: 876px; width: 154px; height: 85px; background: var(--panel); padding: 11px 14px; }
  .box h3 { font-family: "Cabin", sans-serif; font-weight: 400; font-size: 11px; }
  .box-mail h3 { color: var(--green); }
  .box-jobs h3 { color: var(--orange); }
  .box-courses h3 { color: var(--teal); }
  .email-input { margin-top: 5px; height: 14px; background: #fff; border: 1px solid #d6d6d6; font-size: 6px; color: #777; padding: 2px 6px; }
  .subscribe { position: absolute; right: 12px; top: 59px; width: 56px; height: 17px; background: linear-gradient(#4aab32, var(--green-dark)); color: #fff; font-size: 8px; text-align: center; line-height: 17px; border-radius: 2px; }
  .job-links { margin-top: 6px; display: grid; grid-template-columns: 73px 1fr; row-gap: 5px; font-size: 6.2px; color: #444; }
  .job-links span::before { content: "\203A"; margin-right: 3px; }
  .box-courses p { margin-top: 4px; font-size: 6.5px; line-height: 12px; color: #777; }
  .badge { position: absolute; right: 14px; bottom: 8px; display: flex; align-items: center; gap: 2px; font-size: 6px; color: #444; }
  .badge i { width: 7px; height: 7px; background: var(--orange); display: block; }

  .footer { left: 0; top: 985px; width: 686px; height: 175px; background: linear-gradient(var(--footer-top), var(--footer-bot)); border-top: 3px solid #8fd0e4; }
  .footer h4 { position: absolute; top: 26px; font-family: "Cabin", sans-serif; font-weight: 400; font-size: 12px; color: #fff; }
  .fb-box { position: absolute; left: 70px; top: 47px; width: 175px; height: 108px; background: #fff; border-radius: 2px; padding: 8px; }
  .fb-grid { display: grid; grid-template-columns: repeat(4, 37px); gap: 5px 4px; }
  .fb-grid i { display: block; width: 37px; height: 38px; }
  .fb-box small { display: block; margin-top: 3px; font-size: 6px; color: #aaa; }
  .follow { position: absolute; font-size: 7px; color: #fff; display: flex; align-items: center; gap: 7px; }
  .follow i { display: block; width: 19px; height: 19px; background: rgba(255,255,255,.28); border-radius: 2px; }
  .footer-strip { left: 0; top: 1160px; width: 686px; height: 40px; background: var(--footer-strip); color: #e6f4f8; font-size: 7.5px; text-align: center; line-height: 40px; }
  .footer-strip span { margin: 0 3px; }
</style>
</head>
<body>
<div class="page">

  <div class="abs topbar">
    <div class="links">Advertise Job Vacancy <span>:</span> Sign In <span>|</span> Register</div>
  </div>

  <header class="abs header">
    <div class="brand"><span class="brand-mark"></span><span class="brand-name">Lumarinovo</span></div>
    <div class="social-top" aria-label="Social links">
      <i></i><i></i><i></i><i></i><i></i>
    </div>
    <nav class="nav">
      <a href="#">Blog</a><a href="#">For Business</a><a href="#">Events &amp; Partners</a><a href="#">About Us</a><a href="#">Contact</a>
    </nav>
  </header>

  <section class="abs hero">
    <div class="hero-photo" role="img" aria-label="Photo of a smiling woman sitting with a laptop"></div>
    <div class="hero-kicker">Looking for a Career In Beauty..</div>
    <h1 class="hero-title">Find Your Dream Job</h1>
    <div class="search">
      <div class="field select">Jobs</div>
      <div class="field key">Key tittle or company</div>
      <div class="field loc">Locations</div>
      <div class="btn">SEARCH</div>
    </div>
  </section>

  <div class="abs tabs">
    <div class="tab active">Featured Job Vacancies</div>
    <div class="tab">Latest Job Vacancies</div>
    <div class="tab">Job Vacancies</div>
  </div>
  <div class="abs tabs-rule"></div>

  <article class="abs job" style="top:402px">
    <div class="job-logo"><i role="img" aria-label="Salon logo" style="background:#b8a46e;border-radius:50%"></i></div>
    <div class="job-title">Aux. Hairdresser (Escovista) - Santo André (SP)</div>
    <div class="job-meta" style="top:27px">Marta Reis / Opala Hair and Esthetics - Posted by Marta Dos Reis</div>
    <div class="job-city">Santo André</div>
    <div class="job-region">São Paulo, the Federative Republic of Brazil</div>
    <div class="job-date">July 18</div>
    <div class="job-year">2013</div>
  </article>
  <div class="abs rule" style="left:155px;top:462px;width:343px"></div>

  <article class="abs job" style="top:473px">
    <div class="job-logo"><i role="img" aria-label="Salon logo" style="background:#36c2c0"></i></div>
    <div class="job-title">Manicure - Closest subway Vila Madalena - São Paulo (SP)</div>
    <div class="job-meta" style="top:28px">JV Manicure and Waxing - Posted by jobs</div>
    <div class="job-city">Santo André</div>
    <div class="job-region">São Paulo, the Federative Republic of Brazil</div>
    <div class="job-date">July 18</div>
    <div class="job-year">2013</div>
  </article>
  <div class="abs rule" style="left:155px;top:531px;width:343px"></div>

  <article class="abs job" style="top:543px">
    <div class="job-logo"><i role="img" aria-label="Salon logo" style="background:#2d3f7a;border-radius:50%;width:16px;height:16px"></i></div>
    <div class="job-title">Manicure - Jabalpur - São Paulo (SP)</div>
    <div class="job-meta" style="top:15px">Esmalteria Solara - Unit Jabalpur - Posted by nunes_claudia</div>
    <div class="job-city">Santo André</div>
    <div class="job-region">São Paulo, the Federative Republic of Brazil</div>
    <div class="job-date">July 18</div>
    <div class="job-year">2013</div>
  </article>
  <div class="abs rule" style="left:157px;top:603px;width:371px;background:#d8d8d8"></div>

  <nav class="abs pager">
    <span class="wide">Prev</span><span>1</span><span>2</span><span>3</span><span>4</span><span>5</span><span>6</span><span>...</span><span>22</span><span class="wide">Next</span>
  </nav>

  <h2 class="abs section-title" style="left:118px;top:658px">Online Course Aprendi</h2>

  <div class="abs course" style="left:118px;top:681px">
    <div class="course-img" role="img" aria-label="Photo of a student working on a laptop" style="background:linear-gradient(135deg,#f1ece8,#e4c9cf 55%,#8c8a88)"></div>
    <p>Mauris vel lacus vitae felis vestibulum volutpat. Etiam est nunc venenatis</p>
    <span class="btn-orange">READ MORE</span>
  </div>
  <div class="abs course" style="left:273px;top:681px">
    <div class="course-img" role="img" aria-label="Photo of a student at a desk with a laptop" style="background:linear-gradient(135deg,#eeeeee,#9cbf6a 55%,#e8e8e8)"></div>
    <p>Mauris vel lacus vitae felis vestibulum volutpat. Etiam est nunc venenatis</p>
    <span class="btn-orange">READ MORE</span>
  </div>
  <div class="abs course" style="left:428px;top:681px">
    <div class="course-img" role="img" aria-label="Photo of two smiling friends" style="background:linear-gradient(135deg,#ede2d8,#e0b99a 50%,#b98c6c)"></div>
    <p>Mauris vel lacus vitae felis vestibulum volutpat. Etiam est nunc venenatis</p>
    <span class="btn-orange">READ MORE</span>
  </div>

  <div class="abs divider"></div>

  <div class="abs box box-mail" style="left:94px">
    <h3>Assinar Por Email</h3>
    <div class="email-input">email address</div>
    <span class="subscribe">Subscribe</span>
  </div>
  <div class="abs box box-jobs" style="left:262px">
    <h3>Job Vacancy</h3>
    <div class="job-links">
      <span>Assistant Hairdresser</span><span>Designer Eyebrow</span>
      <span>Assistant Cleaning</span><span>Featured</span>
      <span>Hairdresser</span><span>Nurse</span>
    </div>
  </div>
  <div class="abs box box-courses" style="left:431px">
    <h3>Online Courses Aprendi</h3>
    <p>Nunc tempus felis vitae urna. Vivamus porttitor, g. purus nisi eleifend libero, a tempus libero lectus feugiat felis.</p>
    <span class="badge">aprendi<i></i></span>
  </div>

  <footer class="abs footer">
    <h4 style="left:70px">Facenet Feed</h4>
    <div class="fb-box">
      <div class="fb-grid" role="img" aria-label="Grid of member profile photos">
        <i style="background:#c99a80"></i><i style="background:#e2d6cc"></i><i style="background:#b5714f"></i><i style="background:#8d6a4e"></i>
        <i style="background:#6a4a3a"></i><i style="background:#d9a97e"></i><i style="background:#c4a58a"></i><i style="background:#e8ddd2"></i>
      </div>
      <small>facenet page</small>
    </div>

    <h4 style="left:284px">Follow Us</h4>
    <div class="follow" style="left:287px;top:47px"><i></i>On Chirpline</div>
    <div class="follow" style="left:287px;top:72px"><i></i>As RSS Feed</div>
    <div class="follow" style="left:287px;top:97px"><i></i>Shared on Facenet</div>
    <div class="follow" style="left:287px;top:120px"><i></i>On Orbita+</div>
    <div class="follow" style="left:395px;top:47px"><i></i>Pinboardy</div>
    <div class="follow" style="left:395px;top:72px"><i></i>Vidstream</div>
    <div class="follow" style="left:395px;top:97px"><i></i>Workring</div>
    <div class="follow" style="left:395px;top:124px"><i></i>Snapgram</div>
  </footer>

  <div class="abs footer-strip">
    © 2013 www.lumarinovo.com <span>|</span> Term and Conditions <span>|</span> Privacy Statement <span>|</span> Imprint <span>|</span> Glassary
  </div>

</div>
</body>
</html>
```